Double-sided A5 leaflet with photos.

Design A5 leaflet double sided
With emphasis on we are cheaper than our competition as a hook
The colour can be whatever makes it look like a unique brand.
Try and use all the different photos because they are unique.
And put the different photos on there with headlines
Updates

Need extra days to review

Target Market(s)

The idea is it stands out people moving that you can offer different things to like taking their bed apart, taking their old furniture or they just want to move and want two men and the truck. Big or small or piano? Heavy furniture marble table? People who want their bed taken apart put back together again, piano moving, marble table. Moving fridge for washing machine. Moving small truck picture of big truck the poster is people walking past in the street. The pelmo leaflet is delivered to high rise unit blocks with 300 units.

Industry/Entity Type

Furniture removal

Colors
59FF00
82FF00
B8FF75
E3FFCB
F4FFEA

Requirements
Must have
• Try and use all the different photos the screenshot of the Varnex review next to the other photos we put beds together, etc
Nice to have
• It would be nice to have on one side all the different photos with headlines on each one saying what they do EG beds taken apart over the top of a photo .g

```html
<!DOCTYPE html>
<html lang="en">
<head>
<meta charset="utf-8">
<title>Steady Haul – Leaflet</title>
<link href="https://fonts.googleapis.com/css2?family=Alfa+Slab+One&family=Poppins:wght@400;500;600&display=swap" rel="stylesheet">
<style>
  :root{
    --green-dark:#1f4f26;
    --green:#2a6a31;
    --green-light:#4f8f3c;
    --yellow:#f2eb1d;
    --white:#ffffff;
    --ink:#1b1b1b;
    --paper:#f7f8f6;
    --bg:#d5d5d5;
    --rule:#e1e1e1;
  }
  *{box-sizing:border-box;margin:0;padding:0}
  html,body{width:1200px;height:2194px;overflow:hidden;background:var(--bg)}
  body{position:relative;font-family:"Poppins",sans-serif;color:var(--ink)}
  .card{position:absolute;left:50px;width:1100px;height:520px;background:var(--white);overflow:hidden;box-shadow:0 6px 18px rgba(0,0,0,.12)}
  .front{top:527px}
  .back{top:1097px}

  /* front */
  .front-band{position:absolute;left:0;top:0;width:1100px;height:355px;background:linear-gradient(90deg,var(--green-dark),var(--green) 60%,var(--green-dark))}
  .front-base{position:absolute;left:0;top:355px;width:1100px;height:165px;background:linear-gradient(180deg,#fff,var(--paper))}
  .hero-ring{position:absolute;left:45px;top:55px;width:480px;height:480px;border-radius:50%;border:2px solid var(--ink);background:radial-gradient(circle at 50% 45%,var(--green-light),var(--green) 60%,var(--green-dark))}
  .hero-art{position:absolute;left:55px;top:85px;width:500px;height:435px;border-radius:40px 40px 0 0;background:linear-gradient(160deg,rgba(242,235,29,.0) 0%,rgba(242,235,29,.55) 55%,rgba(255,255,255,.7) 100%)}
  .headline{position:absolute;left:597px;top:60px;font-family:"Alfa Slab One",serif;font-weight:400;line-height:1.02;white-space:nowrap}
  .headline .line{display:block;font-size:64px;color:var(--yellow);letter-spacing:1px}
  .headline .big{display:block;font-size:92px;color:var(--white);letter-spacing:2px}
  .contact{position:absolute;left:600px;top:382px;display:flex;align-items:center;gap:20px}
  .brand-dot{width:100px;height:100px;border-radius:50%;background:var(--green);display:flex;align-items:center;justify-content:center;text-align:center;flex:none}
  .brand-dot span{font-family:"Alfa Slab One",serif;color:var(--white);font-size:16px;line-height:1.1}
  .phone-big{font-family:"Alfa Slab One",serif;font-size:40px;color:var(--green);line-height:1;white-space:nowrap}
  .web{font-family:"Alfa Slab One",serif;font-size:16px;color:var(--ink);margin-top:8px;letter-spacing:.5px;white-space:nowrap}

  /* back */
  .back-header{position:absolute;left:0;top:0;width:651px;height:140px;background:var(--green);padding:28px 0 0 44px;font-family:"Alfa Slab One",serif;font-weight:400;font-size:31px;line-height:1.3;letter-spacing:.5px;white-space:nowrap}
  .back-header .y{color:var(--yellow);display:block}
  .back-header .w{color:var(--white);display:block}
  .offers{position:absolute;left:0;top:140px;width:662px;height:325px;background:linear-gradient(180deg,#fff,var(--paper))}
  .divider{position:absolute;top:30px;width:1px;height:255px;background:var(--rule)}
  .offer{position:absolute;top:25px;width:190px;text-align:center}
  .offer-name{height:128px;display:flex;align-items:center;justify-content:center;gap:8px}
  .offer-name .mark{width:20px;height:20px;border-radius:50%;background:var(--green);flex:none}
  .offer-name .label{font-family:"Poppins",sans-serif;font-weight:600;font-size:20px;color:var(--green);line-height:1;white-space:nowrap}
  .price{display:inline-block;background:var(--green);color:var(--white);font-family:"Alfa Slab One",serif;font-size:26px;border-radius:8px;padding:3px 20px;line-height:1.4}
  .price sup{font-size:12px;vertical-align:super;margin-right:3px}
  .note{font-size:16px;line-height:1.32;margin:6px 0}
  .note sup{font-size:10px}
  .strip{position:absolute;left:0;top:465px;width:662px;height:55px;background:var(--green)}
  .strip-yellow{position:absolute;left:0;top:0;height:55px;width:370px;background:var(--yellow);clip-path:polygon(0 0,335px 0,370px 55px,0 55px)}
  .call-tag{position:absolute;left:34px;top:18px;background:var(--green);color:var(--white);font-family:"Alfa Slab One",serif;font-size:10px;padding:4px 8px;border-radius:2px;white-space:nowrap}
  .strip-phone{position:absolute;left:120px;top:11px;font-family:"Alfa Slab One",serif;font-size:24px;line-height:1.3;color:var(--green);white-space:nowrap}
  .strip-web{position:absolute;left:390px;top:17px;font-family:"Alfa Slab One",serif;font-size:15px;color:var(--white);white-space:nowrap}
  .stamp{position:absolute;left:959px;top:26px;width:104px;height:105px;background:#ececec}
  .addr{position:absolute;left:767px;width:296px;height:3px;background:var(--rule)}
</style>
</head>
<body>
  <section class="card front" aria-label="Leaflet front">
    <div class="front-band"></div>
    <div class="front-base"></div>
    <div class="hero-ring"></div>
    <div class="hero-art" role="img" aria-label="Illustrated mover in yellow uniform holding a fragile box in front of a branded removal truck"></div>
    <h1 class="headline">
      <span class="line">VERY VERY</span>
      <span class="line">VERY CHEAP</span>
      <span class="big">MOVERS</span>
    </h1>
    <div class="contact">
      <div class="brand-dot"><span>STEADY<br>HAUL</span></div>
      <div>
        <div class="phone-big">0400 555 123</div>
        <div class="web">WWW.STEADYHAUL.COM.AU</div>
      </div>
    </div>
  </section>

  <section class="card back" aria-label="Leaflet back">
    <h2 class="back-header">
      <span class="y">WE CAN HELP YOU FOR ALL</span>
      <span class="w">DIFFERENT TYPES OF MOVES</span>
    </h2>
    <div class="offers">
      <div class="offer" style="left:15px">
        <div class="offer-name" style="height:100px"><span class="mark"></span><span class="label">Twin Crew</span></div>
        <p class="note">1<sup>st</sup> Hour</p>
        <span class="price"><sup>$</sup>465</span>
        <p class="note">Then Per Hour</p>
        <span class="price"><sup>$</sup>250</span>
      </div>
      <div class="divider" style="left:215px"></div>
      <div class="offer" style="left:230px">
        <div class="offer-name"><span class="mark"></span><span class="label">Solo Van Co</span></div>
        <span class="price"><sup>$</sup>225</span>
        <p class="note">Per Hour Base<br>to Base From<br>Eastvale</p>
      </div>
      <div class="divider" style="left:438px"></div>
      <div class="offer" style="left:452px">
        <div class="offer-name"><span class="mark"></span><span class="label">Steady Haul</span></div>
        <span class="price"><sup>$</sup>170</span>
        <p class="note">Per Hour no<br>base to base<br>change</p>
      </div>
    </div>
    <div class="strip">
      <div class="strip-yellow">
        <span class="call-tag">CALL DIRECT</span>
        <span class="strip-phone">0400 555 123</span>
      </div>
      <span class="strip-web">WWW.STEADYHAUL.COM.AU</span>
    </div>
    <div class="stamp"></div>
    <div class="addr" style="top:218px"></div>
    <div class="addr" style="top:310px"></div>
    <div class="addr" style="top:401px"></div>
  </section>
</body>
</html>
```